Awesome business card design needed

We need a new business card design to go with our new logo.
We are a web development agency that specialises in highly complex back-end integrations as opposed to design, our customers are retailers, hotels, hospitals and any other organisation that has a large online marketing department.
Take a look at our website - www.brenoloft.com for some inspiration.
We want our new business cards to exude class, professionalism and style.
We are likely to choose a high-end card to print them on but we want the design of the card itself to really turn heads.
We have no specific colour requirements, the logo as you will see is a turquoise colour R89 G171 B167 #59aba7 but it can also be in white if you want to make the colour of the card something different.
The information on the card should be:
Name
Position
Tel
email
Potentially a double sided card could have our web address, twitter and FB links.

```html
<!DOCTYPE html>
<html lang="en">
<head>
<meta charset="utf-8">
<title>Brenoloft Business Card</title>
<link rel="stylesheet" href="https://fonts.googleapis.com/css2?family=Questrial&display=swap">
<style>
  :root {
    --teal: #59aba7;
    --teal-deep: #4f9f9b;
    --white: #ffffff;
    --ink: #3e3e42;
    --muted: #6b6b70;
    --rule: #c9c9cc;
    --page: #eeeeec;
  }
  * { margin: 0; padding: 0; box-sizing: border-box; }
  html, body {
    width: 1200px;
    height: 720px;
    overflow: hidden;
    background: var(--page);
    font-family: "Questrial", "Century Gothic", sans-serif;
  }
  .stage {
    width: 1200px;
    height: 720px;
    display: flex;
    align-items: center;
    justify-content: center;
    gap: 40px;
  }
  .card {
    position: relative;
    width: 540px;
    height: 309px;
    overflow: hidden;
    box-shadow: 0 2px 10px rgba(0,0,0,0.12);
  }

  /* Front side */
  .card--front { background: var(--white); }
  .card__wave {
    position: absolute;
    inset: 0;
    width: 100%;
    height: 100%;
  }
  .brand-name {
    color: var(--teal);
    letter-spacing: 1px;
    line-height: 1;
  }
  .card--front .brand-name {
    position: absolute;
    left: 48px;
    top: 120px;
    font-size: 46px;
  }
  .divider {
    position: absolute;
    left: 292px;
    top: 14px;
    width: 1px;
    height: 138px;
    background: linear-gradient(var(--white), var(--rule) 30%, var(--rule) 70%, var(--white));
  }
  .contact {
    position: absolute;
    left: 312px;
    top: 20px;
  }
  .contact__name {
    color: var(--teal);
    font-size: 20px;
    font-weight: 700;
  }
  .contact__position {
    color: var(--ink);
    font-size: 12px;
    margin-top: 1px;
  }
  .contact__list {
    list-style: none;
    margin-top: 14px;
  }
  .contact__item {
    display: flex;
    align-items: center;
    gap: 8px;
    color: var(--ink);
    font-size: 13.5px;
    margin-bottom: 6px;
  }
  .contact__icon { width: 13px; height: 13px; flex: none; }
  .address {
    position: absolute;
    left: 170px;
    bottom: 22px;
    color: var(--white);
    font-size: 13px;
    letter-spacing: 0.3px;
  }

  /* Back side */
  .card--back {
    background: var(--teal);
    text-align: center;
    color: var(--white);
  }
  .card--back .brand-name {
    color: var(--white);
    font-size: 76px;
    padding-top: 88px;
    letter-spacing: 3px;
  }
  .follow {
    margin-top: 34px;
    display: flex;
    align-items: center;
    justify-content: center;
    gap: 8px;
    font-size: 17px;
  }
  .follow__label { margin-right: 4px; }
  .social-square {
    width: 28px;
    height: 28px;
    border-radius: 5px;
    background: var(--white);
    opacity: 0.9;
  }
  .web {
    margin-top: 10px;
    font-size: 16px;
    letter-spacing: 1.5px;
  }
</style>
</head>
<body>
<main class="stage">
  <section class="card card--front" aria-label="Business card front">
    <svg class="card__wave" viewBox="0 0 540 309" preserveAspectRatio="none" aria-hidden="true">
      <path d="M0,250 C170,272 330,205 540,168 L540,309 L0,309 Z" fill="var(--teal)"/>
      <path d="M110,262 C290,250 410,178 540,146 L540,158 C410,192 290,256 110,262 Z" fill="var(--ink)"/>
    </svg>

    <div class="brand-name">brenoloft</div>
    <div class="divider"></div>

    <div class="contact">
      <div class="contact__name">Your Name</div>
      <div class="contact__position">Position</div>
      <ul class="contact__list">
        <li class="contact__item">
          <svg class="contact__icon" viewBox="0 0 16 16" aria-hidden="true">
            <circle cx="8" cy="8" r="7.2" fill="none" stroke="var(--teal)" stroke-width="1.4"/>
            <path d="M5.6,4.4 L7,4.4 L7.4,6.2 L6.5,7 C6.9,8 7.9,9.1 9,9.5 L9.8,8.6 L11.6,9 L11.6,10.4 C8,10.8 5.2,8 5.6,4.4 Z" fill="var(--teal)"/>
          </svg>
          123-456-7890
        </li>
        <li class="contact__item">
          <svg class="contact__icon" viewBox="0 0 16 16" aria-hidden="true">
            <rect x="1" y="3.5" width="14" height="9" rx="1.5" fill="var(--teal)"/>
            <path d="M1.8,4.4 L8,9 L14.2,4.4" fill="none" stroke="var(--white)" stroke-width="1.2"/>
          </svg>
          info@brenoloft.com
        </li>
        <li class="contact__item">
          <svg class="contact__icon" viewBox="0 0 16 16" aria-hidden="true">
            <circle cx="8" cy="8" r="7" fill="var(--teal)"/>
            <ellipse cx="8" cy="8" rx="3" ry="7" fill="none" stroke="var(--white)" stroke-width="1"/>
            <path d="M1,8 H15 M2.5,4.5 H13.5 M2.5,11.5 H13.5" stroke="var(--white)" stroke-width="0.9"/>
          </svg>
          www.brenoloft.com
        </li>
      </ul>
    </div>

    <div class="address">Street Name, City Name, State Zip Code</div>
  </section>

  <section class="card card--back" aria-label="Business card back">
    <div class="brand-name">brenoloft</div>
    <div class="follow">
      <span class="follow__label">Follow Us On:</span>
      <span class="social-square" aria-hidden="true"></span>
      <span class="social-square" aria-hidden="true"></span>
    </div>
    <div class="web">www.brenoloft.com</div>
  </section>
</main>
</body>
</html>
```